Design a Travel and Tourism website

We would like a freelancer to design a website that is essentially easy to use and navigate database providing local information for Travelers about destination countries.

We proposed website would discuss different rates, fees, visa requirement, resort locations, cheap flights, etc. This website should be elegant and modern. Our business name is rovanix.
Some reference websites are zemplorift.ca, brindlefoxhaven.com,
There should be a forum in the website where travell\ers discuss about their first hand tranvel experience to such destinations.

Tourism

```html
<!DOCTYPE html>
<html lang="en">
<head>
<meta charset="utf-8">
<title>Rovanix — Travel and Tourism</title>
<link href="https://fonts.googleapis.com/css2?family=Mulish:wght@400;500;600;700;800&display=swap" rel="stylesheet">
<style>
:root{
  --navy:#053a72;
  --navy-dark:#04305f;
  --ink:#333b45;
  --muted:#5c636b;
  --line:#d9dde2;
  --pale:#eef4fc;
  --panel:rgba(92,92,92,.86);
  --white:#ffffff;
  --accent-red:#d8382e;
}
*{box-sizing:border-box;margin:0;padding:0}
html,body{width:1200px;height:2479px;overflow:hidden}
body{position:relative;font-family:"Mulish",Arial,sans-serif;color:var(--ink);background:var(--white)}
.abs{position:absolute}

/* header */
.topbar{left:0;top:0;width:1200px;height:73px;background:var(--navy)}
.brand{left:99px;top:14px;font-size:36px;font-weight:700;color:var(--white);letter-spacing:.2px}
.account-links{right:99px;top:28px;display:flex;gap:30px;font-size:13px;color:var(--white)}
.account-links span{display:flex;align-items:center;gap:8px}
.mainnav{left:0;top:73px;width:1200px;height:64px;background:var(--white)}
.mainnav ul{position:absolute;left:256px;top:26px;display:flex;gap:0;list-style:none;font-size:13px;color:var(--ink)}
.mainnav li{margin-right:43px}
.book-online{left:996px;top:90px;width:105px;height:28px;background:var(--navy);color:var(--white);border-radius:3px;font-size:12px;display:flex;align-items:center;justify-content:center}

/* hero */
.hero-photo{left:0;top:137px;width:1200px;height:446px;background:linear-gradient(90deg,#d9d8d4 0%,#c9c7c1 45%,#e3e0d8 62%,#b48a60 74%,#efece6 88%,#d7d2c6 100%)}
.search-panel{left:99px;top:177px;width:628px;height:363px;background:var(--panel)}
.mode-btn{width:53px;height:43px;background:#8b8b8b;border-radius:4px;top:23px;display:flex;align-items:center;justify-content:center}
.mode-btn.active{background:#9a9a9a}
.combo-tabs{left:51px;top:83px;display:flex;gap:3px}
.combo-tabs span{font-size:11px;color:var(--white);background:#727272;padding:0 6px;height:32px;line-height:32px;border-radius:3px}
.combo-tabs span.active{background:var(--navy)}
.field-label{font-size:11.5px;color:var(--white);font-weight:600}
.field{height:28px;background:var(--white);border-radius:2px;font-size:11px;color:#8a9097;display:flex;align-items:center;padding-left:8px;gap:6px}
.select::after{content:"";margin-left:auto;margin-right:9px;width:6px;height:6px;border-right:2px solid #333;border-bottom:2px solid #333;transform:rotate(45deg) translateY(-2px)}
.select{color:#333;font-size:13px}
.check-row{left:51px;top:262px;display:flex;align-items:center;gap:10px;font-size:11.5px;color:var(--white)}
.check-row i{width:16px;height:16px;background:#cfcfcf;border-radius:3px;display:block}
.advanced{left:51px;top:290px;font-size:11.5px;color:#9cc3f0}
.search-btn{left:222px;top:304px;width:94px;height:33px;background:var(--navy);color:var(--white);border-radius:3px;font-size:15px;display:flex;align-items:center;justify-content:center;font-weight:600}

/* deals */
.section-title{font-size:26px;font-weight:700;color:var(--navy)}
.deal-card{top:707px;width:300px;height:255px;border:1px solid var(--line);background:var(--white)}
.deal-card .photo{height:176px;width:100%}
.deal-card p{text-align:center;font-size:16.5px;line-height:23px;color:var(--ink);padding-top:20px}
.deal-banner{display:flex;align-items:center;justify-content:center;text-align:center;color:var(--white);font-weight:700;font-size:20px;line-height:30px}

/* popular */
.popular-band{left:0;top:1025px;width:1200px;height:972px;background:var(--pale)}
.place-card{width:311px;background:var(--white)}
.place-card .photo{width:100%;height:273px}
.place-card h3{text-align:center;font-size:24px;font-weight:600;color:#555b61;height:55px;line-height:52px}
.offer{display:flex;align-items:center;justify-content:center;color:var(--white);font-size:44px;font-weight:700}
.view-all{left:460px;top:1886px;width:281px;height:68px;border:2px solid var(--navy);color:var(--navy);font-size:21px;font-weight:600;display:flex;align-items:center;justify-content:center}

/* services */
.block-title{font-size:26px;font-weight:500;color:#222}
.services-box{left:99px;top:2103px;width:313px;height:289px;background:#f4f4f4;border-radius:4px}
.service-row{left:30px;width:250px;height:55px;display:flex;align-items:center;gap:22px;font-size:13.5px;color:var(--ink);border-bottom:1px solid var(--line)}
.service-row:last-child{border-bottom:0}
.service-row.highlight{color:var(--accent-red)}
.service-row svg{width:30px;height:30px;flex:none}
.slider{left:474px;top:2103px;width:622px;height:289px;border-radius:6px;overflow:hidden;background:linear-gradient(180deg,#3f8fde 0%,#6fb1ee 28%,#1e5da4 45%,#144b8c 70%,#f2f2f2 74%,#e6e6e6 100%)}
.slider-arrow{top:2128px;width:30px;height:30px;border-radius:50%;background:var(--white);display:flex;align-items:center;justify-content:center}

/* footer */
.footer{left:0;top:2425px;width:1200px;height:54px;background:var(--navy);color:var(--white);font-size:12px}
.footer .copy{position:absolute;left:99px;top:20px;font-size:10.5px}
.footer ul{position:absolute;right:28px;top:19px;display:flex;list-style:none;gap:30px}
</style>
</head>
<body>

<header>
  <div class="abs topbar"></div>
  <div class="abs brand">Rovanix</div>
  <div class="abs account-links">
    <span><svg width="14" height="14" viewBox="0 0 14 14"><path d="M7 1v8M3.5 4.5L7 1l3.5 3.5M1 10v3h12v-3" stroke="#fff" stroke-width="1.6" fill="none"/></svg>Sign In</span>
    <span><svg width="14" height="14" viewBox="0 0 14 14"><rect x="1" y="1" width="12" height="12" rx="2" stroke="#fff" stroke-width="1.6" fill="none"/><path d="M4 7l2 2 4-4" stroke="#fff" stroke-width="1.6" fill="none"/></svg>My Booking</span>
    <span><svg width="14" height="14" viewBox="0 0 14 14"><path d="M2 3c1-2 3-2 4 0l-1 2c1 2 2 3 4 4l2-1c2 1 2 3 0 4-5 0-9-4-9-9z" fill="#fff"/></svg>Customer Support</span>
  </div>
  <nav class="abs mainnav">
    <ul><li>Flights</li><li>Hotels</li><li>Cars</li><li>Vacations</li><li>Cruises</li><li>Business Class Flights</li><li>Featured Deals</li></ul>
  </nav>
  <div class="abs book-online">Book Online</div>
</header>

<section class="hero">
  <div class="abs hero-photo" role="img" aria-label="Child in an aviator cap and scarf flying a toy airplane in a bright room"></div>
  <form class="abs search-panel">
    <div class="abs mode-btn active" style="left:51px"><svg width="26" height="26" viewBox="0 0 24 24"><path d="M2 13l8-2 5-7h2l-2 7 6 0 2-2h1l-1 4 1 4h-1l-2-2h-6l2 7h-2l-5-7-8-2z" fill="#0a4a90"/></svg></div>
    <div class="abs mode-btn" style="left:122px"><svg width="24" height="24" viewBox="0 0 24 24"><rect x="3" y="2" width="18" height="20" fill="none" stroke="#222" stroke-width="2"/><path d="M7 6h2M11 6h2M15 6h2M7 10h2M11 10h2M15 10h2M7 14h2M11 14h2M15 14h2" stroke="#222" stroke-width="2"/></svg></div>
    <div class="abs mode-btn" style="left:193px"><svg width="28" height="26" viewBox="0 0 28 26"><path d="M3 11a11 9 0 0 1 22 0z" fill="#222"/><path d="M14 11v9M3 22h22" stroke="#222" stroke-width="2"/></svg></div>
    <div class="abs mode-btn" style="left:265px"><svg width="30" height="22" viewBox="0 0 30 22"><path d="M3 16v-6l4-6h16l4 6v6z" fill="none" stroke="#222" stroke-width="2.2"/><circle cx="9" cy="17" r="3" fill="#222"/><circle cx="21" cy="17" r="3" fill="#222"/></svg></div>
    <div class="abs mode-btn" style="left:336px"><svg width="22" height="22" viewBox="0 0 22 22"><rect x="2" y="2" width="18" height="18" rx="2" fill="#222"/><path d="M6 8h10M6 11h10M6 14h10" stroke="#9a9a9a" stroke-width="1.6"/></svg></div>

    <div class="abs combo-tabs"><span class="active">Flight + Hotel</span><span>Flight + Hotel + Car</span><span>Flight + Car</span><span>Hotel + Car</span></div>

    <div class="abs field-label" style="left:51px;top:132px">Flying From</div>
    <div class="abs field-label" style="left:322px;top:132px">Flying To</div>
    <div class="abs field" style="left:51px;top:153px;width:255px"><svg width="10" height="13" viewBox="0 0 10 13"><path d="M5 12S1 7 1 5a4 4 0 0 1 8 0c0 2-4 7-4 7z" fill="none" stroke="#999" stroke-width="1.3"/></svg>City or Airport</div>
    <div class="abs field" style="left:322px;top:153px;width:252px"><svg width="10" height="13" viewBox="0 0 10 13"><path d="M5 12S1 7 1 5a4 4 0 0 1 8 0c0 2-4 7-4 7z" fill="none" stroke="#999" stroke-width="1.3"/></svg>City or Airport</div>

    <div class="abs field-label" style="left:51px;top:193px">Departing</div>
    <div class="abs field-label" style="left:190px;top:193px">Returning</div>
    <div class="abs field-label" style="left:331px;top:193px">Rooms</div>
    <div class="abs field-label" style="left:384px;top:193px">Adults (18+)</div>
    <div class="abs field-label" style="left:471px;top:193px">Children (0-17)</div>
    <div class="abs field" style="left:51px;top:215px;width:129px"><svg width="10" height="10" viewBox="0 0 10 10"><rect x="1" y="2" width="8" height="7" fill="none" stroke="#999"/></svg>mm/dd/yyyy</div>
    <div class="abs field" style="left:190px;top:215px;width:129px"><svg width="10" height="10" viewBox="0 0 10 10"><rect x="1" y="2" width="8" height="7" fill="none" stroke="#999"/></svg>mm/dd/yyyy</div>
    <div class="abs field select" style="left:331px;top:215px;width:43px">1</div>
    <div class="abs field select" style="left:384px;top:215px;width:76px">2</div>
    <div class="abs field select" style="left:471px;top:215px;width:86px">0</div>

    <div class="abs check-row"><i></i>I Only need a hotel for part of my stay</div>
    <div class="abs advanced">Advanced Options ▴</div>
    <div class="abs field select" style="left:51px;top:311px;width:131px;font-size:11px;color:#666">Economy/Coach</div>
    <div class="abs search-btn">Search</div>
  </form>
</section>

<section class="deals">
  <h2 class="abs section-title" style="left:99px;top:637px">Today's Top Deals</h2>
  <article class="abs deal-card" style="left:99px">
    <div class="photo" role="img" aria-label="Stacked suitcases at sunset with a plane taking off" style="background:linear-gradient(180deg,#4f7fb7 0%,#a5b8c8 50%,#e1a86a 75%,#6b4a33 100%)"></div>
    <p>40% Discount On All<br>Business Flights</p>
  </article>
  <article class="abs deal-card" style="left:451px">
    <div class="photo deal-banner" role="img" aria-label="Weathered teal wood texture" style="background:linear-gradient(135deg,#2f6f74,#1f575c 60%,#3b7a73)">Make Our Customer Happy<br>With This Festival Season</div>
    <p>50% Discount On Golden<br>Membership Card</p>
  </article>
  <article class="abs deal-card" style="left:800px">
    <div class="photo" role="img" aria-label="Hands showing an engagement ring over a wooden bench" style="background:linear-gradient(135deg,#8d8d8d,#c8bfb7 50%,#8a8a8a)"></div>
    <p>50% Discount On Newly<br>Married Couple</p>
  </article>
</section>

<section class="popular">
  <div class="abs popular-band"></div>
  <h2 class="abs section-title" style="left:0;width:1200px;text-align:center;top:1083px;font-size:29px;font-weight:600">View Our Popular Place To Visit</h2>

  <article class="abs place-card" style="left:99px;top:1150px">
    <div class="photo offer" role="img" aria-label="Taj Mahal under a hazy sky" style="background:linear-gradient(180deg,#6d6a62,#8b7d66 55%,#3c4030)">20 % OFF</div>
    <h3>Taj Mahal</h3>
  </article>
  <article class="abs place-card" style="left:440px;top:1150px">
    <div class="photo" role="img" aria-label="Snowy mountains reflected in a turquoise lake" style="background:linear-gradient(180deg,#3e78c4 0%,#c9d3db 30%,#7d8a8e 50%,#2b5a4a 65%,#5fa9c5 100%)"></div>
    <h3>Banff &amp; Lake Louise</h3>
  </article>
  <article class="abs place-card" style="left:790px;top:1150px">
    <div class="photo" role="img" aria-label="Glass skyscraper in London under a blue sky" style="background:linear-gradient(180deg,#8ec5e6 0%,#c1def0 50%,#4e7f8f 80%,#2b4e5c 100%)"></div>
    <h3>London</h3>
  </article>

  <article class="abs place-card" style="left:96px;top:1514px">
    <div class="photo" role="img" aria-label="Dubai skyline and highway interchange" style="background:linear-gradient(180deg,#6a87a8 0%,#a8aeb2 45%,#5a5550 75%,#3a3632 100%)"></div>
    <h3>Dubai</h3>
  </article>
  <article class="abs place-card" style="left:437px;top:1514px">
    <div class="photo" role="img" aria-label="Statue of Liberty against a pale sky" style="background:linear-gradient(180deg,#e9d9a8 0%,#cdd3b2 40%,#6f9c8a 70%,#5a4a3c 100%)"></div>
    <h3>New York</h3>
  </article>
  <article class="abs place-card" style="left:787px;top:1514px">
    <div class="photo" role="img" aria-label="Historic German riverside city with boats" style="background:linear-gradient(180deg,#3e8fd8 0%,#a7c9e3 30%,#b9794a 55%,#2c8ab0 80%,#1e6f99 100%)"></div>
    <h3>Germany</h3>
  </article>

  <div class="abs view-all">View All Collections</div>
</section>

<section class="services">
  <h2 class="abs block-title" style="left:99px;top:2050px">Customer Services</h2>
  <div class="abs services-box">
    <div class="abs service-row highlight" style="top:7px"><svg viewBox="0 0 30 30"><rect x="8" y="5" width="14" height="7" fill="none" stroke="#222" stroke-width="2"/><rect x="4" y="11" width="22" height="10" rx="2" fill="none" stroke="#222" stroke-width="2"/><rect x="9" y="18" width="12" height="7" fill="#fff" stroke="#222" stroke-width="2"/></svg>Print Your Ticket</div>
    <div class="abs service-row" style="top:63px"><svg viewBox="0 0 30 30"><circle cx="15" cy="15" r="13" fill="#222"/><rect x="9" y="8" width="10" height="13" fill="#fff"/><path d="M16 17l6 6M22 17l-6 6" stroke="#fff" stroke-width="2"/></svg>Cancellation</div>
    <div class="abs service-row" style="top:118px"><svg viewBox="0 0 30 30"><circle cx="15" cy="15" r="12" fill="none" stroke="#222" stroke-width="2" stroke-dasharray="3 2"/><path d="M15 8v14M18 10h-4a2.5 2.5 0 0 0 0 5h2a2.5 2.5 0 0 1 0 5h-5" stroke="#222" stroke-width="2" fill="none"/></svg>Check Refund Status</div>
    <div class="abs service-row" style="top:173px"><svg viewBox="0 0 30 30"><path d="M3 17l9-3 6-9h3l-3 9 6-1 2-3h2l-1 5 1 5h-2l-2-3-6-1 3 9h-3l-6-9z" fill="#222" transform="rotate(-20 15 15)"/></svg>Check Flight Status</div>
    <div class="abs service-row" style="top:228px"><svg viewBox="0 0 30 30"><circle cx="15" cy="15" r="13" fill="#222"/><circle cx="15" cy="9" r="2" fill="#fff"/><rect x="13" y="13" width="4" height="10" fill="#fff"/></svg>FAQ</div>
  </div>

  <h2 class="abs block-title" style="left:481px;top:2050px">Places To Visit</h2>
  <div class="abs slider" role="img" aria-label="Traveller in a sun hat sitting on a white terrace above a blue sea bay"></div>
  <div class="abs slider-arrow" style="left:492px;top:2228px"><svg width="12" height="12" viewBox="0 0 12 12"><path d="M8 2L4 6l4 4" stroke="#222" stroke-width="2" fill="none"/></svg></div>
  <div class="abs slider-arrow" style="left:998px;top:2228px"><svg width="12" height="12" viewBox="0 0 12 12"><path d="M4 2l4 4-4 4" stroke="#222" stroke-width="2" fill="none"/></svg></div>
</section>

<footer class="abs footer">
  <div class="copy">©2017 Rovanix . All rights reserved.</div>
  <ul><li>Live Help</li><li>Site Feedback</li><li>Newsletter Signup</li><li>Free App Download</li><li>Quick Links</li><li>C12</li></ul>
</footer>

</body>
</html>
```